New Business Card Design Project

We require a business card design for Vexalund, a newly established Indian company.
Our focus is on the development, manufacturing, and export of a diverse array of pharmaceutical products on a global scale. The card should convey a professional appearance, as our primary markets are in Africa, China, and Southeast Asian nations.
We envision a two-sided business card, with the reverse side dedicated to a logo set against a solid color or an elegantly designed pattern. The corners should be rounded. We would appreciate seeing both horizontal and vertical design options. We trust the designer to utilize their expertise in creating this design.

The content for the business card is included in the attached Word file.

Target Market(s)

Our primary markets are in Africa, China, and Southeast Asian, Latin America, Maldives, Sri Lanka

Industry/Entity Type

Pharmaceutical Manufacturing and Export

Contact Information for Business Card

Colors

Designer to choose colors to be used in the design.

Requirements
Must have
• The reverse side of the business card features solely the logo along with the tagline, "Wellness Within Reach."
Should not have
• The logo should not exceed two instances, encompassing both the front and back sides of the card.

```html
<!DOCTYPE html>
<html lang="en">
<head>
<meta charset="utf-8">
<title>Vexalund Business Card</title>
<link href="https://fonts.googleapis.com/css2?family=Montserrat:wght@400;500;600;700;800&display=swap" rel="stylesheet">
<style>
  :root {
    --brand-blue: #2a9fd9;
    --brand-blue-deep: #1f86c2;
    --band-blue: #3a95d6;
    --ink: #2b2b2b;
    --paper: #ffffff;
    --stage: #e4e7eb;
    --emboss: #eef0f2;
  }
  * { margin: 0; padding: 0; box-sizing: border-box; }
  html, body { width: 1200px; height: 900px; overflow: hidden; }
  body {
    background: var(--stage);
    font-family: "Montserrat", sans-serif;
    position: relative;
  }
  .card {
    position: absolute;
    top: 290px;
    width: 560px;
    height: 320px;
    border-radius: 22px;
    overflow: hidden;
    box-shadow: 0 10px 28px rgba(0,0,0,0.18);
  }
  /* Back side */
  .card-back {
    left: 27px;
    background: var(--brand-blue);
  }
  .back-pattern {
    position: absolute;
    inset: 0;
    background: linear-gradient(135deg, #4fb0e0 0%, var(--brand-blue) 45%, var(--brand-blue-deep) 100%);
  }
  .back-divider {
    position: absolute;
    left: 0; right: 0; top: 160px;
    height: 1px;
    background: rgba(255,255,255,0.18);
  }
  .back-brand {
    position: absolute;
    right: 46px;
    top: 96px;
    display: flex;
    align-items: center;
    gap: 10px;
    color: var(--paper);
    font-weight: 700;
    font-size: 26px;
  }
  .back-brand .dot {
    width: 14px; height: 14px;
    border-radius: 50%;
    background: var(--paper);
  }
  .tagline {
    position: absolute;
    left: 0; right: 0;
    top: 230px;
    text-align: center;
    color: var(--paper);
    font-weight: 600;
    font-size: 15px;
    letter-spacing: 0.3px;
  }
  /* Front side */
  .card-front {
    left: 613px;
    background: var(--paper);
  }
  .emboss-area {
    position: absolute;
    right: 30px;
    top: 24px;
    width: 220px;
    height: 230px;
    border-radius: 18px;
    background: radial-gradient(circle at 60% 55%, var(--emboss) 0%, #f7f8f9 60%, var(--paper) 100%);
  }
  .company {
    position: absolute;
    left: 34px;
    top: 42px;
    color: var(--brand-blue);
    font-weight: 800;
    font-size: 40px;
    letter-spacing: -0.5px;
  }
  .person-name {
    position: absolute;
    left: 36px;
    top: 104px;
    color: var(--brand-blue);
    font-weight: 700;
    font-size: 19px;
  }
  .person-role {
    position: absolute;
    left: 36px;
    top: 132px;
    color: var(--ink);
    font-weight: 500;
    font-size: 12px;
  }
  .contact-list {
    position: absolute;
    left: 36px;
    top: 168px;
    list-style: none;
    color: var(--ink);
    font-size: 12px;
    font-weight: 500;
    line-height: 1.35;
  }
  .contact-list li {
    display: flex;
    align-items: center;
    gap: 8px;
    margin-bottom: 3px;
  }
  .contact-list .icon { width: 12px; height: 12px; flex: none; fill: var(--brand-blue); }
  .contact-list .address { padding-left: 20px; display: block; }
  .front-band {
    position: absolute;
    left: 0; bottom: 0;
    width: 560px; height: 30px;
  }
</style>
</head>
<body>

  <section class="card card-back" aria-label="Card back">
    <div class="back-pattern" role="img" aria-label="Repeating capsule pattern in tonal blues"></div>
    <div class="back-divider"></div>
    <div class="back-brand">
      <span class="dot"></span>
      <span class="brand-name">Vexalund</span>
    </div>
    <p class="tagline">Wellness Within Reach</p>
  </section>

  <section class="card card-front" aria-label="Card front">
    <div class="emboss-area" role="img" aria-label="Blind-embossed brand decoration"></div>

    <h1 class="company">Vexalund</h1>
    <p class="person-name">Arjun K. Malhotra</p>
    <p class="person-role">CEO</p>

    <ul class="contact-list">
      <li>
        <svg class="icon" viewBox="0 0 12 12" aria-hidden="true"><path d="M1 4c0-1.5 2-2.5 5-2.5S11 2.5 11 4v1H8.5V4h-5v1H1z M2.5 6h7l1 4.5h-9z M6 7a1.2 1.2 0 1 0 0.01 0z"/></svg>
        <span>+919400012345</span>
      </li>
      <li>
        <svg class="icon" viewBox="0 0 12 12" aria-hidden="true"><path d="M1 2.5h10v7H1z M1.5 3l4.5 3.5L10.5 3" stroke="#fff" stroke-width="0.9"/></svg>
        <span>arjun@vexalund.com</span>
      </li>
      <li>
        <svg class="icon" viewBox="0 0 12 12" aria-hidden="true"><circle cx="6" cy="6" r="5"/><path d="M1 6h10M6 1c-2 2.5-2 7.5 0 10M6 1c2 2.5 2 7.5 0 10" stroke="#fff" stroke-width="0.8" fill="none"/></svg>
        <span>www.vexalund.com</span>
      </li>
      <li class="address">12, Sunrise Colony,<br>Nagpur, 440010, India</li>
    </ul>

    <svg class="front-band" viewBox="0 0 560 30" preserveAspectRatio="none" aria-hidden="true">
      <rect x="0" y="22" width="560" height="8" fill="var(--band-blue)"/>
      <polygon points="300,22 560,6 560,22" fill="var(--band-blue)"/>
    </svg>
  </section>

</body>
</html>
```